Business Cards for IT Consulting Company (Managed Service Provider)

I am looking to have some business cards printed and would like some designs. We are an IT Consulting company based in Vancouver BC. I would like a nice clean and modern look to the cards. I have uploaded all the versions of my logo so parts can be used as needed. Here is a snippit from our website homepage:

Quillbrook Networks Ltd. is an IT Solutions Partner located in Vancouver BC, Canada. We offer IT solutions and support to customers in the greater Vancouver Area. With expertise in Microsoft platforms, as well as Linux and Mac OSX and over 12 years experience in the IT industry, Quillbrook Networks is dedicated to offering our clients top quality service and products. We take pride in the solutions we offer our customers. The greatest compliment a client can give us is to recommend our services.

Quillbrook Networks Ltd. offers a wide range of IT services from onsite service to remote support and managed service solutions. This allows clients to choose the support path that best suits their company’s needs. Supporting many different sized companies from small to enterprise level over the past 12 years Quillbrook Networks has the experience and expertise needed to ensure things run smoothly. Allowing our clients to focus on doing business.

Revolutionizing the way IT services are delivered.

Quillbrook Networks is dedicated to providing our clients with IT solutions that work and grow with them for years to come. This philosophy helps save money in the long run instead of replacing equipment constantly. Far too often IT solutions are not well thought out and while possibly solving the problem at hand, require replacement due to growth or quality within a very short time frame. Quillbrook Networks takes pride in providing solutions that will last and be able to accommodate growth without the need for replacement.

Industry/Entity Type

Information Technology

Contact Information for Business Card

Quillbrook Networks Ltd.
(Employee Name)
Eml: (Employees Email Address)
Web: quillbrook.me
Ph: 604-555-0148

Font styles to use
Serif
Sans Serif

Requirements
Must have
• The Company logo and company colors.
Nice to have
• - Our tag line: "Revolutionizing IT Services" or "Revolutionizing the way IT services are delivered."
• - Also I really like the idea of nature and technology together blending which is sort of where my logo came from so integrating that somehow onto the business cards would be great.

```html
<!DOCTYPE html>
<html lang="en">
<head>
<meta charset="utf-8">
<title>Quillbrook Networks Ltd. — Business Cards</title>
<link rel="stylesheet" href="https://fonts.googleapis.com/css2?family=Montserrat:wght@500;600&family=Open+Sans:wght@400;600;700&display=swap">
<style>
  :root {
    --backdrop: #2c2e33;
    --brand-blue: #00a0dc;
    --card-white: #ffffff;
    --card-shade: #eef0f2;
    --ink-grey: #555a5f;
    --ink-dark: #3c3f43;
  }
  * { margin: 0; padding: 0; box-sizing: border-box; }
  html, body { width: 1200px; height: 864px; overflow: hidden; }
  body {
    background: var(--backdrop);
    position: relative;
    font-family: "Open Sans", Arial, sans-serif;
  }
  .card {
    position: absolute;
    width: 610px;
    height: 349px;
    border-radius: 3px;
    box-shadow: 0 6px 18px rgba(0,0,0,0.45);
  }

  /* Front of card */
  .card-front {
    left: 205px;
    top: 40px;
    background: var(--brand-blue);
    color: var(--card-white);
  }
  .front-wordmark {
    position: absolute;
    left: 165px;
    top: 105px;
    font-family: "Montserrat", Arial, sans-serif;
    font-weight: 600;
    line-height: 1;
  }
  .front-wordmark .wordmark-name { font-size: 54px; letter-spacing: 0.5px; display: block; }
  .front-wordmark .wordmark-sub { font-size: 17px; letter-spacing: 1px; display: block; margin-top: 2px; }
  .tagline {
    position: absolute;
    left: 165px;
    top: 222px;
    font-size: 15px;
    font-weight: 700;
  }

  /* Back of card */
  .card-back {
    left: 200px;
    top: 405px;
    background: linear-gradient(180deg, var(--card-white) 0%, var(--card-shade) 100%);
  }
  .back-logo {
    position: absolute;
    left: 55px;
    top: 55px;
    display: flex;
    align-items: center;
    gap: 18px;
    color: var(--brand-blue);
    font-family: "Montserrat", Arial, sans-serif;
    font-weight: 600;
    line-height: 1;
  }
  .logo-square {
    width: 64px;
    height: 64px;
    border: 3px solid var(--brand-blue);
  }
  .back-logo .wordmark-name { font-size: 54px; display: block; }
  .back-logo .wordmark-sub { font-size: 17px; letter-spacing: 1px; display: block; margin-top: 2px; }

  .name-rule {
    position: absolute;
    left: 0;
    right: 0;
    top: 176px;
    display: flex;
    align-items: center;
  }
  .name-rule .rule { height: 1.5px; background: var(--brand-blue); }
  .name-rule .rule-long { flex: 1; }
  .name-rule .rule-short { width: 34px; }
  .person-name {
    font-size: 21px;
    font-weight: 600;
    padding: 0 10px;
    transform: translateY(12px);
    color: var(--ink-dark);
  }
  .person-name .first { color: var(--brand-blue); }

  .contact-list {
    position: absolute;
    right: 34px;
    top: 225px;
    list-style: none;
    text-align: right;
  }
  .contact-list li {
    display: flex;
    justify-content: flex-end;
    align-items: center;
    gap: 10px;
    font-size: 15px;
    color: var(--ink-grey);
    line-height: 25px;
  }
  .contact-list svg { width: 14px; height: 14px; fill: var(--brand-blue); }
</style>
</head>
<body>

  <section class="card card-front" aria-label="Card front">
    <div class="front-wordmark">
      <span class="wordmark-name">quillbrook</span>
      <span class="wordmark-sub">NETWORKS LTD.</span>
    </div>
    <p class="tagline">Revolutionizing IT Services</p>
  </section>

  <section class="card card-back" aria-label="Card back">
    <div class="back-logo">
      <span class="logo-square" aria-hidden="true"></span>
      <div>
        <span class="wordmark-name">quillbrook</span>
        <span class="wordmark-sub">NETWORKS LTD.</span>
      </div>
    </div>

    <div class="name-rule">
      <span class="rule rule-long"></span>
      <span class="person-name"><span class="first">Daniel</span> Porter</span>
      <span class="rule rule-short"></span>
    </div>

    <ul class="contact-list">
      <li>604-555-0148
        <svg viewBox="0 0 24 24" aria-hidden="true"><path d="M6.6 10.8a15.1 15.1 0 0 0 6.6 6.6l2.2-2.2a1 1 0 0 1 1-.25 11.4 11.4 0 0 0 3.6.57 1 1 0 0 1 1 1V20a1 1 0 0 1-1 1A17 17 0 0 1 3 4a1 1 0 0 1 1-1h3.5a1 1 0 0 1 1 1c0 1.25.2 2.45.57 3.57a1 1 0 0 1-.25 1z"/></svg>
      </li>
      <li>info@quillbrook.me
        <svg viewBox="0 0 24 24" aria-hidden="true"><path d="M2 5h20v14H2z" opacity=".9"/><path d="M2 5l10 8 10-8" fill="none" stroke="#fff" stroke-width="2"/></svg>
      </li>
      <li>www.quillbrook.me
        <svg viewBox="0 0 24 24" aria-hidden="true"><circle cx="12" cy="12" r="10"/><path d="M2 12h20M12 2c3 3 3 17 0 20M12 2c-3 3-3 17 0 20" fill="none" stroke="#fff" stroke-width="1.5"/></svg>
      </li>
    </ul>
  </section>

</body>
</html>
```